New Business Card Design for Manufacturing

We are an engineering/manufacturing company that offers Advanced machining/assembly/engineering services, as well as innovative products for the heavy duty engine cooling markets.

We are looking to get a new business card designed that is clean and modern looking, but still fits the wide range of technical/skilled work we do.

- We hope to use this design as the base for other design work in new Presentations, web, and print work.

Industry/Entity Type

Engineering

Contact Information for Business Card

Our preferred color of blue is (RGB) 22/71/159 but can vary slightly from that color. Our content will be our Logo and full company name (Vantrell Forge Works, Inc.), company address, name, job title, phone number with extension, cell number, fax number, website, and email address on the cards.
We'd like the full company name next to the logo, but we are open to other interpretations of that layout.
Preferably, we would like the back side to be clean with just our logo, and the front to contain all of the contact information.

Colors
2f74b4
0355a3
85abd2

Requirements
Must have
• - Logo, company name, needed content - We are open to interpretation beyond that.
• - Standard size business card.
• - Horizontal orientation.
• - Enough space for lengthy names / job titles (for example, a job title could read "Directory of Human Resources" or "V.P. of Governmental Affairs"). We need this to look clean, whether the title be short (CEO) or long (as described above).

```html
<!DOCTYPE html>
<html lang="en">
<head>
<meta charset="utf-8">
<title>Vantrell Forge Works – Business Card</title>
<link href="https://fonts.googleapis.com/css2?family=Roboto:wght@400;500;700;900&display=swap" rel="stylesheet">
<style>
  :root {
    --blue-deep: #16479f;
    --blue-mid: #0355a3;
    --blue-light: #2f74b4;
    --blue-soft: #85abd2;
    --paper: #f4f5f6;
    --ink: #4a4d52;
    --rule: #8a8d92;
    --stage: #2b2c2e;
    --white: #ffffff;
  }
  * { margin: 0; padding: 0; box-sizing: border-box; }
  html, body { width: 1200px; height: 900px; overflow: hidden; }
  body {
    background: var(--stage);
    font-family: "Roboto", Arial, sans-serif;
    position: relative;
  }
  .card {
    position: absolute;
    left: 320px;
    width: 560px;
    height: 320px;
    border-radius: 4px;
    box-shadow: 0 14px 34px rgba(0,0,0,.45);
    overflow: hidden;
  }
  /* Back side */
  .card-back {
    top: 90px;
    background: radial-gradient(circle at 70% 80%, var(--blue-light) 0%, var(--blue-mid) 45%, var(--blue-deep) 100%);
    display: flex;
    align-items: center;
    justify-content: center;
    gap: 22px;
  }
  .brand-name {
    font-weight: 900;
    font-size: 46px;
    letter-spacing: 1px;
    color: var(--white);
  }
  .company-name {
    color: var(--white);
    font-weight: 700;
    font-size: 14px;
    line-height: 1.2;
    letter-spacing: .5px;
    text-transform: uppercase;
  }
  .company-name small { font-size: 8px; font-weight: 700; }
  /* Front side */
  .card-front {
    top: 490px;
    background: var(--paper);
    color: var(--ink);
  }
  .front-brand {
    position: absolute;
    left: 170px;
    top: 40px;
    display: flex;
    align-items: center;
    gap: 10px;
  }
  .front-brand .brand-name { color: var(--blue-light); font-size: 40px; }
  .brand-square { width: 14px; height: 14px; background: var(--blue-light); }
  .front-rule {
    position: absolute;
    left: 40px;
    right: 40px;
    top: 150px;
    height: 1px;
    background: var(--rule);
  }
  .contact-list {
    position: absolute;
    left: 40px;
    top: 168px;
    list-style: none;
    font-size: 12.5px;
    line-height: 20px;
  }
  .contact-list li { display: flex; align-items: center; gap: 8px; }
  .contact-list svg { width: 11px; height: 11px; fill: var(--blue-mid); flex: none; }
  .person {
    position: absolute;
    right: 40px;
    top: 92px;
    text-align: right;
  }
  .person-name { color: var(--blue-light); font-weight: 700; font-size: 22px; }
  .person-title { font-size: 12.5px; margin-top: 2px; }
  .address {
    position: absolute;
    right: 40px;
    top: 168px;
    text-align: right;
    font-size: 12.5px;
    line-height: 20px;
  }
</style>
</head>
<body>
  <section class="card card-back" aria-label="Business card back">
    <span class="brand-name">VANTRELL</span>
    <p class="company-name">Vantrell<br>Forge<br>Works <small>Inc.</small></p>
  </section>

  <section class="card card-front" aria-label="Business card front">
    <div class="front-brand">
      <span class="brand-square"></span>
      <span class="brand-name">VANTRELL</span>
    </div>

    <div class="person">
      <p class="person-name">Marcus Hale</p>
      <p class="person-title">V.P. of Governmental Affairs</p>
    </div>

    <div class="front-rule"></div>

    <ul class="contact-list">
      <li><svg viewBox="0 0 24 24"><path d="M6.6 10.8a15.1 15.1 0 0 0 6.6 6.6l2.2-2.2a1 1 0 0 1 1-.25 11.4 11.4 0 0 0 3.6.57 1 1 0 0 1 1 1V20a1 1 0 0 1-1 1A17 17 0 0 1 3 4a1 1 0 0 1 1-1h3.5a1 1 0 0 1 1 1c0 1.25.2 2.45.57 3.57a1 1 0 0 1-.25 1z"/></svg>415 208 6630</li>
      <li><svg viewBox="0 0 24 24"><path d="M7 1h10a2 2 0 0 1 2 2v18a2 2 0 0 1-2 2H7a2 2 0 0 1-2-2V3a2 2 0 0 1 2-2zm0 3v14h10V4z"/></svg>415 208 6631</li>
      <li><svg viewBox="0 0 24 24"><path d="M6 2h10v5H6zM3 8h18a1 1 0 0 1 1 1v9h-4v4H6v-4H2V9a1 1 0 0 1 1-1zm5 8v4h8v-4z"/></svg>415 208 6631</li>
      <li><svg viewBox="0 0 24 24"><path d="M2 5h20v14H2zm2 2v.5l8 5 8-5V7z"/></svg>info@vantrellforge.com</li>
      <li><svg viewBox="0 0 24 24"><path d="M12 2a10 10 0 1 0 0 20 10 10 0 0 0 0-20zm6.9 6h-2.9a15 15 0 0 0-1.4-3.6A8 8 0 0 1 18.9 8zM12 4c.8 1.2 1.5 2.5 1.9 4h-3.8c.4-1.5 1.1-2.8 1.9-4zM4.3 14a8 8 0 0 1 0-4h3.4a16 16 0 0 0 0 4zm.8 2h2.9a15 15 0 0 0 1.4 3.6A8 8 0 0 1 5.1 16zM8 8H5.1a8 8 0 0 1 4.3-3.6A15 15 0 0 0 8 8zm4 12c-.8-1.2-1.5-2.5-1.9-4h3.8c-.4 1.5-1.1 2.8-1.9 4zm2.3-6H9.7a14 14 0 0 1 0-4h4.6a14 14 0 0 1 0 4zm.3 5.6a15 15 0 0 0 1.4-3.6h2.9a8 8 0 0 1-4.3 3.6zm1.7-5.6a16 16 0 0 0 0-4h3.4a8 8 0 0 1 0 4z"/></svg>www.vantrellforge.com</li>
    </ul>

    <p class="address">Level 5, 27 Harlow Lane<br>Carlton, VIC 3053</p>
  </section>
</body>
</html>
```